Card Design for my dog training business Brightpaw Obedience

Need a business card design for my dog training business with my new logo. Want the card to come off professional yet fun. Want it to be very eye catchy as well. I normally have these at vet clinics, pet stores, and groomers. so need it to look better than my competitors.
Target Market(s)
dog owners
Industry/Entity Type
Dog Training
Contact Information for Business Card
needs logo, my name and info
Font styles to use
Serif
Colors
0255a3
ffffff
ec1f27
000000
333333
fbfbfb
Requirements
Must have
- Brightpaw Obedience
- Felix Orland
- 415 903 2276
- info@brightpawobedience.example
- www.brightpawobedience.example

```html
<!DOCTYPE html>
<html lang="en">
<head>
<meta charset="utf-8">
<title>Brightpaw Obedience – Business Card</title>
<link href="https://fonts.googleapis.com/css2?family=Tinos&family=Lato:wght@400&display=swap" rel="stylesheet">
<style>
  :root {
    --backdrop: #8e8e8e;
    --card-light: #fbfbfb;
    --card-dark: #333333;
    --pattern-tone: #3a3a3a;
    --ink: #000000;
    --ink-soft: #333333;
    --divider: #c9c9c9;
    --reverse-ink: #e4e4e4;
  }
  * { margin: 0; padding: 0; box-sizing: border-box; }
  html, body { width: 1200px; height: 802px; overflow: hidden; }
  body { background: var(--backdrop); position: relative; }

  .card {
    position: absolute;
    top: 274px;
    width: 443px;
    height: 264px;
    overflow: hidden;
    box-shadow: 0 3px 6px rgba(0,0,0,0.35);
  }
  .card--front { left: 136px; background: var(--card-light); }
  .card--back  { left: 624px; background: var(--card-dark); }

  .brand-block {
    position: absolute;
    left: 46px;
    top: 106px;
    width: 120px;
    text-align: center;
    font-family: "Tinos", serif;
    font-size: 20px;
    font-weight: 400;
    line-height: 1.15;
    color: var(--ink);
  }

  .divider {
    position: absolute;
    left: 205px;
    top: 80px;
    width: 1px;
    height: 104px;
    background: var(--divider);
  }

  .holder-name {
    position: absolute;
    left: 224px;
    top: 86px;
    font-family: "Tinos", serif;
    font-size: 16px;
    font-weight: 400;
    letter-spacing: 0.3px;
    color: var(--ink);
    white-space: nowrap;
  }

  .contact-list {
    position: absolute;
    left: 224px;
    top: 132px;
    list-style: none;
    font-family: "Lato", sans-serif;
    font-size: 11px;
    line-height: 16px;
    color: var(--ink-soft);
    white-space: nowrap;
  }
  .contact-list li { display: flex; align-items: center; gap: 5px; }
  .contact-list svg { width: 8px; height: 8px; flex: none; fill: var(--ink-soft); }

  .back-pattern {
    position: absolute;
    inset: 0;
    background: radial-gradient(circle at 50% 50%, var(--pattern-tone), var(--card-dark) 80%);
  }
  .back-brand {
    position: absolute;
    left: 0;
    right: 0;
    top: 118px;
    text-align: center;
    font-family: "Tinos", serif;
    font-size: 14px;
    line-height: 1.15;
    color: var(--reverse-ink);
  }
</style>
</head>
<body>
  <section class="card card--front">
    <div class="brand-block">Brightpaw<br>Obedience</div>
    <div class="divider"></div>
    <h1 class="holder-name">FELIX ORLAND</h1>
    <ul class="contact-list">
      <li>
        <svg viewBox="0 0 10 10" aria-hidden="true"><path d="M1 3.5C1 2 2.5 1.5 5 1.5S9 2 9 3.5L7.5 4 7 3H3L2.5 4ZM2.5 5H7.5L8.5 8.5H1.5Z"/></svg>
        415 903 2276
      </li>
      <li>
        <svg viewBox="0 0 10 10" aria-hidden="true"><path d="M0.5 2H9.5V8H0.5ZM1 2.6V3.2L5 5.8 9 3.2V2.6Z" fill-rule="evenodd"/></svg>
        info@brightpawobedience.example
      </li>
      <li>
        <svg viewBox="0 0 10 10" aria-hidden="true"><circle cx="5" cy="5" r="4.5"/></svg>
        www.brightpawobedience.example
      </li>
    </ul>
  </section>

  <section class="card card--back">
    <div class="back-pattern" role="img" aria-label="Faint repeating brand mark pattern across the dark card back"></div>
    <div class="back-brand">Brightpaw<br>Obedience</div>
  </section>
</body>
</html>
```